Oil and Gas Exploration and Production company needs a business card design

We need a business card design using our logo and colors in the logo. We want a mainstream design.

```html
<!DOCTYPE html>
<html lang="en">
<head>
<meta charset="utf-8">
<title>Solara Oil &amp; Gas – Business Card</title>
<link rel="stylesheet" href="https://fonts.googleapis.com/css2?family=Arimo:wght@400;700&display=swap">
<style>
  :root {
    --ink: #0d0d0d;
    --paper: #ffffff;
    --gold: #d4b53c;
    --gold-text: #e0c04a;
    --stage: #e9e4da;
    --light-text: #f2f2f2;
  }
  * { margin: 0; padding: 0; box-sizing: border-box; }
  html, body { width: 1200px; height: 780px; overflow: hidden; }
  body {
    background: var(--stage);
    font-family: "Arimo", Arial, sans-serif;
    display: flex;
    align-items: center;
    justify-content: center;
    gap: 40px;
  }
  .card {
    position: relative;
    width: 540px;
    height: 309px;
    overflow: hidden;
    box-shadow: 0 8px 24px rgba(0,0,0,0.18);
  }

  /* Front */
  .card-front { background: var(--paper); }
  .brand {
    position: absolute;
    left: 0; right: 0; top: 92px;
    display: flex;
    align-items: center;
    justify-content: center;
    gap: 14px;
  }
  .brand-dot {
    width: 34px; height: 34px;
    border-radius: 50%;
    background: var(--gold);
  }
  .brand-name {
    font-weight: 700;
    font-size: 44px;
    letter-spacing: -0.5px;
    color: var(--ink);
  }
  .web-band {
    position: absolute;
    left: 0; right: 0; bottom: 38px;
    height: 40px;
    background: var(--gold);
    display: flex;
    align-items: center;
    justify-content: flex-end;
    padding-right: 34px;
  }
  .web-address {
    font-size: 15px;
    color: var(--ink);
    letter-spacing: 0.3px;
  }

  /* Back */
  .card-back { background: var(--ink); color: var(--light-text); }
  .holder {
    position: absolute;
    left: 40px; top: 56px;
  }
  .holder-name {
    font-weight: 700;
    font-size: 22px;
    color: var(--light-text);
  }
  .holder-title {
    font-size: 17px;
    color: var(--gold-text);
    margin-top: 2px;
  }
  .contact {
    position: absolute;
    left: 200px; bottom: 42px;
    list-style: none;
    font-size: 17px;
    line-height: 25px;
  }
  .contact-line { display: flex; align-items: center; gap: 8px; }
  .contact-icon { width: 19px; height: 19px; flex: none; }
</style>
</head>
<body>

  <section class="card card-front" aria-label="Card front">
    <div class="brand">
      <span class="brand-dot"></span>
      <span class="brand-name">Solara Oil &amp; Gas</span>
    </div>
    <div class="web-band">
      <span class="web-address">www.solaraenergy.com</span>
    </div>
  </section>

  <section class="card card-back" aria-label="Card back">
    <div class="holder">
      <p class="holder-name">Daniel Reyes</p>
      <p class="holder-title">President &amp; CEO</p>
    </div>
    <ul class="contact">
      <li class="contact-line">PO BOX 456, Harbor Street</li>
      <li class="contact-line">4th Lane, Leeds</li>
      <li class="contact-line">
        <svg class="contact-icon" viewBox="0 0 20 20" aria-hidden="true">
          <circle cx="10" cy="10" r="9" fill="none" stroke="var(--gold)" stroke-width="1.6"/>
          <path d="M7 5.5l2 2-1.2 1.4a6 6 0 0 0 3.3 3.3L12.5 11l2 2-1.3 1.5C9.5 14.3 5.7 10.5 5.5 6.8z" fill="var(--gold)"/>
        </svg>
        (321) 555 0199
      </li>
      <li class="contact-line">
        <svg class="contact-icon" viewBox="0 0 20 20" aria-hidden="true">
          <circle cx="10" cy="10" r="9" fill="none" stroke="var(--gold)" stroke-width="1.6"/>
          <rect x="5" y="6.5" width="10" height="7" fill="var(--gold)"/>
          <path d="M5 6.5l5 4 5-4" fill="none" stroke="var(--ink)" stroke-width="1"/>
        </svg>
        info@solaraenergy.com
      </li>
    </ul>
  </section>

</body>
</html>
```